Business card - Harbor Crest Builders

Design a business card utilizing the given logo.
colors we like: Black, greys, Teal, blues.
Tri color card, horizontal orientation likely
Logo and name likely best on top.
Info on card:

Dennis Farrow
#8 - 4815 Alder Ridge Blvd.
Surrey, B.C. V3K 2R9

778.555.0193
dennisfarrow@tellmail.ca

Slogan: "Building Dreams"

We are a construction company that specializes in new home construction on the West coast of BC Canada. Open Concepts designs of high end homes.

```html
<!DOCTYPE html>
<html lang="en">
<head>
<meta charset="utf-8">
<title>Harbor Crest Builders – Business Card</title>
<link href="https://fonts.googleapis.com/css2?family=Saira:wght@400;500&display=swap" rel="stylesheet">
<style>
  :root {
    --stage: #1f1f20;
    --card-light: #f7f7f7;
    --card-mid: #dcdcdc;
    --ink: #2b2b2b;
    --ink-soft: #555555;
    --rule: #8a8a8a;
    --icon-bg: #3a3a3a;
    --icon-fg: #f2f2f2;
  }
  * { box-sizing: border-box; margin: 0; padding: 0; }
  html, body {
    width: 1200px; height: 754px; overflow: hidden;
    background: var(--stage);
    font-family: "Saira", sans-serif;
    color: var(--ink);
  }
  .stage {
    position: relative; width: 1200px; height: 754px;
    display: flex; align-items: center; justify-content: center; gap: 40px;
  }
  .card {
    position: relative; width: 530px; height: 303px;
    background: radial-gradient(ellipse at 55% 45%, var(--card-light) 0%, #ececec 55%, var(--card-mid) 100%);
    box-shadow: 0 10px 30px rgba(0,0,0,.55);
  }

  /* Front: contact side */
  .person { position: absolute; left: 250px; top: 52px; }
  .person__name { font-size: 17px; font-weight: 500; letter-spacing: .8px; text-transform: uppercase; }
  .person__title { font-size: 10px; letter-spacing: 1.2px; text-transform: uppercase; color: var(--ink-soft); margin-top: -2px; }
  .contact-list { position: absolute; left: 250px; top: 112px; list-style: none; }
  .contact-list li { display: flex; align-items: center; gap: 8px; font-size: 12.5px; letter-spacing: .5px; margin-bottom: 7px; }
  .icon {
    width: 15px; height: 15px; border-radius: 50%;
    background: var(--icon-bg); display: flex; align-items: center; justify-content: center; flex: none;
  }
  .icon svg { width: 9px; height: 9px; fill: var(--icon-fg); stroke: var(--icon-fg); }

  .front-brand { position: absolute; left: 40px; top: 178px; display: flex; align-items: center; gap: 12px; }
  .brand-dot { width: 38px; height: 38px; border-radius: 50%; background: var(--ink); flex: none; }
  .brand-name {
    font-size: 19px; font-weight: 400; letter-spacing: 1.5px; text-transform: uppercase;
    color: var(--ink); line-height: 1.15;
  }

  .address { position: absolute; left: 300px; top: 212px; width: 200px; }
  .address__rule { height: 1px; background: var(--rule); margin-bottom: 26px; }
  .address__line { display: flex; align-items: center; gap: 8px; font-size: 11px; letter-spacing: .4px; }

  /* Back: brand side */
  .back-brand {
    position: absolute; inset: 0;
    display: flex; align-items: center; justify-content: center; gap: 22px;
  }
  .back-brand .brand-dot { width: 62px; height: 62px; }
  .back-brand__rule { width: 1px; height: 60px; background: var(--rule); }
  .back-brand .brand-name { font-size: 26px; letter-spacing: 2px; }
</style>
</head>
<body>
<main class="stage">

  <section class="card card--front" aria-label="Card front">
    <div class="person">
      <p class="person__name">Dennis Farrow</p>
      <p class="person__title">General Manager</p>
    </div>

    <ul class="contact-list">
      <li>
        <span class="icon"><svg viewBox="0 0 10 10"><path d="M2 1l2 2-1 1.2c.6 1.2 1.6 2.2 2.8 2.8L7 6l2 2-1.3 1.3C4.5 9 1 5.5.7 2.3z" stroke="none"/></svg></span>
        778.555.0193
      </li>
      <li>
        <span class="icon"><svg viewBox="0 0 10 10"><rect x="1" y="2.5" width="8" height="5" stroke="none"/><path d="M1 2.5l4 3 4-3" fill="none" stroke-width=".9" style="stroke:#3a3a3a"/></svg></span>
        dennisfarrow@tellmail.ca
      </li>
      <li>
        <span class="icon"><svg viewBox="0 0 10 10"><circle cx="5" cy="5" r="3.8" fill="none" stroke-width=".9"/><path d="M1.2 5h7.6M5 1.2c-2 2.4-2 5.2 0 7.6M5 1.2c2 2.4 2 5.2 0 7.6" fill="none" stroke-width=".8"/></svg></span>
        www.harborcrestbuilders.ca
      </li>
    </ul>

    <div class="front-brand">
      <span class="brand-dot"></span>
      <p class="brand-name">Harbor Crest<br>Builders</p>
    </div>

    <div class="address">
      <div class="address__rule"></div>
      <p class="address__line">
        <span class="icon"><svg viewBox="0 0 10 10"><path d="M5 .8a3 3 0 0 1 3 3C8 6 5 9.4 5 9.4S2 6 2 3.8a3 3 0 0 1 3-3z" stroke="none"/><circle cx="5" cy="3.8" r="1.1" style="fill:#3a3a3a" stroke="none"/></svg></span>
        #8 - 4815 Alder Ridge Blvd. V3K 2R9
      </p>
    </div>
  </section>

  <section class="card card--back" aria-label="Card back">
    <div class="back-brand">
      <span class="brand-dot"></span>
      <span class="back-brand__rule"></span>
      <p class="brand-name">Harbor Crest<br>Builders</p>
    </div>
  </section>

</main>
</body>
</html>
```